Need Business Card for our Real Estate Business with Sales Executive's Picture

PANTONE 484 C ( RED)

PANTONE 2766 C ( BLUE

Industry/Entity Type

Real Estate

Contact Information for Business Card

Name, Mobile, email, & picture of Person
Agency Phone, address, Web address

Requirements
Must have
• Our Logo Colours, Agent Picture,

```html
<!DOCTYPE html>
<html lang="en">
<head>
<meta charset="utf-8">
<title>Mesa Ridge Realty – Business Card</title>
<link rel="stylesheet" href="https://fonts.googleapis.com/css2?family=Open+Sans:wght@400;600;700&display=swap">
<style>
  :root {
    --page-bg: #3b3b3d;
    --card-dark: #1e1e20;
    --card-back: #242426;
    --brand-red: #c8262b;
    --brand-blue: #16286a;
    --text-light: #ffffff;
    --emboss: #2e2e31;
  }
  * { margin: 0; padding: 0; box-sizing: border-box; }
  html, body { width: 799px; height: 1200px; overflow: hidden; }
  body {
    background: var(--page-bg);
    font-family: "Open Sans", Arial, sans-serif;
    color: var(--text-light);
    position: relative;
  }
  .card {
    position: absolute;
    left: 80px;
    width: 640px;
    height: 366px;
    border-radius: 6px;
    overflow: hidden;
    box-shadow: 0 10px 28px rgba(0,0,0,.45);
  }
  .card-front { top: 110px; background: var(--card-dark); }
  .card-back  { top: 720px; background: var(--card-back); }

  /* Front */
  .front-wordmark {
    position: absolute;
    left: 0; right: 0; top: 120px;
    text-align: center;
    font-size: 52px;
    font-weight: 700;
    letter-spacing: 8px;
    color: var(--emboss);
  }
  .front-web {
    position: absolute;
    left: 0; right: 0; top: 262px;
    display: flex;
    align-items: center;
    justify-content: center;
    gap: 18px;
    font-size: 17px;
  }
  .front-web .rule { width: 60px; height: 3px; background: var(--brand-red); }

  /* Back */
  .wave-band {
    position: absolute;
    left: 0; top: 0;
    width: 640px; height: 200px;
    background: linear-gradient(160deg, rgba(36,36,38,0) 30%, rgba(22,40,106,.55) 55%, var(--brand-blue) 75%);
  }
  .brand {
    position: absolute;
    left: 52px; top: 112px;
    display: flex; align-items: center; gap: 12px;
  }
  .brand-square { width: 12px; height: 12px; background: var(--brand-red); }
  .brand-name {
    font-size: 38px;
    font-weight: 400;
    letter-spacing: 5px;
    line-height: 1;
  }
  .brand-tag {
    position: absolute;
    left: 76px; top: 160px;
    font-size: 9px;
    letter-spacing: 4px;
  }
  .contact-list {
    position: absolute;
    left: 40px; top: 188px;
    list-style: none;
    font-size: 15px;
    line-height: 22px;
  }
  .contact-list li { display: flex; align-items: center; gap: 8px; }
  .contact-list svg { width: 12px; height: 12px; fill: var(--brand-red); flex: none; }
  .agent {
    position: absolute;
    right: 34px; top: 74px;
    text-align: right;
  }
  .agent-name { font-size: 22px; font-weight: 700; line-height: 1.3; }
  .agent-title { font-size: 15px; }
  .agent-photo {
    position: absolute;
    left: 420px; top: 206px;
    width: 200px; height: 160px;
    background: linear-gradient(180deg, #6b4a38 0%, #3a3a40 45%, #1f3a8a 100%);
  }
</style>
</head>
<body>

<section class="card card-front">
  <div class="front-wordmark">MESA RIDGE</div>
  <div class="front-web">
    <span class="rule"></span>
    <span>www.mesaridgerealty.com</span>
    <span class="rule"></span>
  </div>
</section>

<section class="card card-back">
  <div class="wave-band" role="img" aria-label="Decorative blue and red wave band"></div>

  <div class="brand">
    <span class="brand-square"></span>
    <span class="brand-name">MESA RIDGE</span>
  </div>
  <div class="brand-tag">REALTY</div>

  <ul class="contact-list">
    <li><svg viewBox="0 0 12 12"><path d="M2 1h3l1 3-2 1a7 7 0 0 0 3 3l1-2 3 1v3c-6 0-9-4-9-9z"/></svg>555.201.3478</li>
    <li><svg viewBox="0 0 12 12"><path d="M2 1h3l1 3-2 1a7 7 0 0 0 3 3l1-2 3 1v3c-6 0-9-4-9-9z"/></svg>555-310-7624</li>
    <li><svg viewBox="0 0 12 12"><path d="M0 2h12v8H0z"/></svg>mesaridgerealty.com</li>
    <li><svg viewBox="0 0 12 12"><circle cx="6" cy="6" r="6"/></svg>dwhitfield@mesaridgerealty.com</li>
    <li>48 Canyon Way #210, Golden, CO 80401</li>
  </ul>

  <div class="agent">
    <div class="agent-name">Dana Whitfield</div>
    <div class="agent-title">Managing Director</div>
  </div>

  <div class="agent-photo" role="img" aria-label="Portrait photo of the agent in a blue suit"></div>
</section>

</body>
</html>
```